Professional Photography Business cards

I need business cards that include my logo which I have uploaded. I run a photography business. I am open to ideas but I would like one side to have my logo and the other side to have my contact info. I don't have a website made but I do own a website domain. I have uploaded 2 different logo color schemes. My business colors are Blue, black , and white.

Business Name
Business Phone Number
Business Email
Business Website address
Instagram

Industry/Entity Type

Professional Photography

Contact Information for Business Card

Phone Number: 916-384-7702 email: info@tlane-studio.example Instagram: @t.lanestudio website doman- www.tlane-studio.example

Requirements
Must have
• I like the idea of a business card with a full black background front and back of card. My colors must include royal blue, black, and white

```html
<!DOCTYPE html>
<html lang="en">
<head>
<meta charset="utf-8">
<title>T. Lane Photography — Business Cards</title>
<link rel="stylesheet" href="https://fonts.googleapis.com/css2?family=Arimo:wght@400&display=swap">
<style>
  :root {
    --backdrop: #2b2b2d;
    --royal-blue: #0610a8;
    --card-shadow: rgba(0, 0, 0, 0.55);
    --ink: #ffffff;
  }
  * { margin: 0; padding: 0; box-sizing: border-box; }
  html, body {
    width: 1200px;
    height: 1015px;
    overflow: hidden;
    background: var(--backdrop);
    font-family: "Arimo", Arial, sans-serif;
    color: var(--ink);
  }
  .canvas {
    position: relative;
    width: 1200px;
    height: 1015px;
  }
  .card {
    position: absolute;
    width: 760px;
    height: 434px;
    background: var(--royal-blue);
    box-shadow: 0 18px 40px var(--card-shadow);
  }
  .card--front { left: 220px; top: 54px; }
  .card--back  { left: 220px; top: 528px; }

  .brand {
    position: absolute;
    display: flex;
    align-items: center;
    gap: 18px;
  }
  .brand__mark {
    flex: none;
    border: 3px solid var(--ink);
    border-radius: 50%;
  }
  .brand__name {
    font-weight: 400;
    letter-spacing: 0.14em;
    text-transform: uppercase;
    white-space: nowrap;
  }

  .card--front .brand {
    left: 50%;
    top: 50%;
    transform: translate(-50%, -50%);
  }
  .card--front .brand__mark { width: 58px; height: 58px; }
  .card--front .brand__name { font-size: 34px; }

  .card--back .brand {
    right: 48px;
    top: 64px;
  }
  .card--back .brand__mark { width: 40px; height: 40px; }
  .card--back .brand__name { font-size: 23px; }

  .contact-list {
    position: absolute;
    left: 48px;
    bottom: 48px;
    list-style: none;
    display: flex;
    flex-direction: column;
    gap: 14px;
  }
  .contact-list__item {
    display: flex;
    align-items: center;
    gap: 12px;
    font-size: 19px;
  }
  .contact-list__icon {
    width: 26px;
    height: 26px;
    flex: none;
  }

  .social-handle {
    position: absolute;
    right: 48px;
    bottom: 142px;
    display: flex;
    align-items: center;
    gap: 10px;
    font-size: 19px;
  }
  .social-handle__dot {
    width: 22px;
    height: 22px;
    border-radius: 50%;
    background: var(--ink);
  }
</style>
</head>
<body>
<main class="canvas">

  <section class="card card--front" aria-label="Card front">
    <div class="brand">
      <span class="brand__mark"></span>
      <span class="brand__name">T. Lane Photography</span>
    </div>
  </section>

  <section class="card card--back" aria-label="Card back">
    <div class="brand">
      <span class="brand__mark"></span>
      <span class="brand__name">T. Lane Photography</span>
    </div>

    <div class="social-handle">
      <span>@t.lanestudio</span>
      <span class="social-handle__dot"></span>
    </div>

    <ul class="contact-list">
      <li class="contact-list__item">
        <svg class="contact-list__icon" viewBox="0 0 26 26" aria-hidden="true">
          <circle cx="13" cy="13" r="13" fill="#fff"/>
          <path d="M9 7.5c.6-.4 1.3-.2 1.6.4l1 2c.2.5.1 1-.3 1.3l-.8.6c.6 1.4 1.6 2.5 3 3.2l.7-.7c.4-.4.9-.5 1.4-.2l1.9 1.1c.6.3.7 1 .3 1.6l-.7.9c-.6.7-1.6.9-2.5.5-3.1-1.3-5.4-3.8-6.5-6.9-.3-.9 0-1.9.7-2.4z" fill="#0610a8"/>
        </svg>
        <span>916-384-7702</span>
      </li>
      <li class="contact-list__item">
        <svg class="contact-list__icon" viewBox="0 0 26 26" aria-hidden="true">
          <circle cx="13" cy="13" r="13" fill="#fff"/>
          <rect x="6.5" y="8.5" width="13" height="9" fill="none" stroke="#0610a8" stroke-width="1.6"/>
          <path d="M6.5 8.5l6.5 5 6.5-5" fill="none" stroke="#0610a8" stroke-width="1.6"/>
        </svg>
        <span>info@tlane-studio.example</span>
      </li>
      <li class="contact-list__item">
        <svg class="contact-list__icon" viewBox="0 0 26 26" aria-hidden="true">
          <circle cx="13" cy="13" r="13" fill="#fff"/>
          <g fill="none" stroke="#0610a8" stroke-width="1.4">
            <circle cx="13" cy="13" r="6.5"/>
            <ellipse cx="13" cy="13" rx="3" ry="6.5"/>
            <path d="M6.5 13h13M7.5 9.8h11M7.5 16.2h11"/>
          </g>
        </svg>
        <span>www.tlane-studio.example</span>
      </li>
    </ul>
  </section>

</main>
</body>
</html>
```